Business Card Design For A Renovation Contractor Company

We need a business card for a new company based in Singapore, our company name is "RB Tolvane". We are a renovation contractor that builds designs into reality. We build more of F&B restaurants, retail stores and commercial offices. We work very closely with designers. The final design should communicate to our client that we are a company that you can trust, that will plan and complete your project without giving you a headache. I like my client to remember my company as "RB". The beauty of SIMPLE is important.

Industry/Entity Type

Contractor

Requirements
Nice to have
• Black or Red base

```html
<!DOCTYPE html>
<html lang="en">
<head>
<meta charset="utf-8">
<title>RB Tolvane – Business Card</title>
<link href="https://fonts.googleapis.com/css2?family=Arimo:wght@400;700&family=Josefin+Sans:wght@400&display=swap" rel="stylesheet">
<style>
  :root {
    --brand-red: #ec2227;
    --ink: #1c1c1c;
    --paper: #ffffff;
    --stage: #e9e9ee;
    --muted: #555555;
  }
  * { margin: 0; padding: 0; box-sizing: border-box; }
  html, body { width: 1200px; height: 987px; overflow: hidden; }
  body {
    background: var(--stage);
    font-family: "Arimo", Arial, sans-serif;
    position: relative;
  }
  .card {
    position: absolute;
    left: 215px;
    width: 770px;
    height: 440px;
    border-radius: 26px;
    overflow: hidden;
    box-shadow: 0 6px 18px rgba(0,0,0,0.12);
  }
  /* Front */
  .card-front { top: 36px; background: var(--paper); }
  .brand {
    position: absolute;
    left: 300px;
    top: 78px;
    width: 330px;
  }
  .brand-row { display: flex; align-items: center; gap: 14px; }
  .brand-dot {
    width: 52px; height: 52px; border-radius: 50%;
    background: var(--brand-red);
    flex: none;
  }
  .brand-name {
    font-size: 50px;
    font-weight: 400;
    color: var(--ink);
    letter-spacing: -1px;
    line-height: 1;
    white-space: nowrap;
  }
  .brand-rule { height: 2px; background: var(--ink); margin-top: 8px; }
  .brand-tagline {
    font-size: 21px;
    color: var(--ink);
    margin-top: 3px;
    letter-spacing: 0.3px;
    white-space: nowrap;
  }
  .info-band {
    position: absolute;
    left: 0; right: 0;
    top: 200px;
    height: 178px;
    background: var(--brand-red);
    color: var(--paper);
  }
  .person {
    position: absolute;
    right: 430px;
    top: 28px;
    text-align: right;
  }
  .person-name { font-size: 30px; font-weight: 700; }
  .person-title { font-size: 20px; margin-top: 4px; }
  .divider {
    position: absolute;
    left: 360px;
    top: 24px;
    width: 2px;
    height: 118px;
    background: rgba(255,255,255,0.75);
  }
  .contacts {
    position: absolute;
    left: 385px;
    top: 22px;
    list-style: none;
    font-size: 22px;
    line-height: 32px;
  }
  .address {
    position: absolute;
    left: 0; right: 0;
    top: 378px;
    height: 62px;
    display: flex;
    align-items: center;
    justify-content: center;
    font-size: 22px;
    color: var(--muted);
  }
  /* Back */
  .card-back {
    top: 511px;
    background: var(--brand-red);
    color: var(--paper);
  }
  .back-mark {
    position: absolute;
    left: 0; right: 0;
    top: 92px;
    display: flex;
    flex-direction: column;
    align-items: center;
    gap: 22px;
  }
  .back-circle {
    width: 150px; height: 150px; border-radius: 50%;
    border: 16px solid var(--paper);
  }
  .back-name {
    font-size: 46px;
    font-weight: 400;
    line-height: 1;
  }
  .back-web {
    position: absolute;
    left: 0; right: 0;
    bottom: 48px;
    text-align: center;
    font-family: "Josefin Sans", Arial, sans-serif;
    font-size: 24px;
    letter-spacing: 6px;
  }
</style>
</head>
<body>
  <section class="card card-front">
    <div class="brand">
      <div class="brand-row">
        <span class="brand-dot"></span>
        <span class="brand-name">RB Tolvane</span>
      </div>
      <div class="brand-rule"></div>
      <div class="brand-tagline">from drawing to doorway</div>
    </div>
    <div class="info-band">
      <div class="person">
        <div class="person-name">Your Name</div>
        <div class="person-title">Title</div>
      </div>
      <div class="divider"></div>
      <ul class="contacts">
        <li>p: 123-456-7890</li>
        <li>c: 123-456-7890</li>
        <li>e: info@rbtolvane.com</li>
        <li>w: www.rbtolvane.com</li>
      </ul>
    </div>
    <div class="address">Door No. Street Name City Name, State, Zip Code.</div>
  </section>

  <section class="card card-back">
    <div class="back-mark">
      <span class="back-circle"></span>
      <span class="back-name">RB Tolvane</span>
    </div>
    <div class="back-web">www.rbtolvane.com</div>
  </section>
</body>
</html>
```